Business Card Design for Translation Company - Rush

Rush job for a business card designing for a company doing international translations, several Asian and western languages. Already have a logo design (see attached) to use as the basis of the business card design. For the card, we also need the full company name, address, email, and phone number. In addition, my name as I will be the one handing out the cards.

For the logo design, we think the white background would be best. But we will consider using the dark background if you have a great idea for it.

The attached jpeg design has just been approved, but the designer has not yet finalized the file. When we select our final applicant, we will send the finalized file. (Nothing changes except the quality of the data.)

The phone number may change and if so, we will send the new one when we select our applicant.

We must complete the entire process and have a design ready to go to print no later than 01:00 am August 3, New York (East Coast) time.

We look forward to your participation in the project,
Dale

Target Market(s)

Translation clients worldwide.

Industry/Entity Type

Business

Contact Information for Business Card

Company details:

Korvanta Translations International, Ltd.

#207-2836 Wexholm Avenue, Victoria, BC, Canada V9T3K2

jquell@korvantatranslations.example

+1-888-604-7321

Font styles to use
Sans Serif

Requirements
Must have
• Company name, address, email and phone number.
• Also my name:
• Gordon R. Quell
• Director
Nice to have
• Not a demand, but please consider creatively using the horizontal bar.
Should not have
• Cluttered of jumbled appearance.

```html
<!DOCTYPE html>
<html lang="en">
<head>
<meta charset="utf-8">
<title>Korvanta Translations – Business Card</title>
<link rel="stylesheet" href="https://fonts.googleapis.com/css2?family=Lato:wght@400;700&display=swap">
<style>
  :root {
    --bg: #e9e4dc;
    --paper: #ffffff;
    --ink: #3a3a3a;
    --ink-soft: #5a5a5a;
    --orange: #e57a22;
    --charcoal: #333333;
    --black: #161616;
    --white: #ffffff;
  }
  * { margin: 0; padding: 0; box-sizing: border-box; }
  html, body { width: 1200px; height: 1024px; overflow: hidden; }
  body {
    background: var(--bg);
    font-family: "Lato", sans-serif;
    position: relative;
  }
  .card {
    position: absolute;
    width: 700px;
    height: 400px;
    overflow: hidden;
    box-shadow: 0 10px 30px rgba(0,0,0,0.18);
  }
  .card--front { left: 80px; top: 70px; background: var(--paper); }
  .card--back { left: 420px; top: 550px; background: var(--black); }

  .swoosh { position: absolute; inset: 0; }

  .brand {
    display: flex;
    align-items: center;
    gap: 14px;
  }
  .brand__dot {
    width: 34px; height: 34px; border-radius: 50%;
    background: var(--orange);
    flex: none;
  }
  .brand__name {
    font-weight: 700;
    font-size: 26px;
    letter-spacing: 4px;
    text-transform: uppercase;
    white-space: nowrap;
  }
  .brand-bar { height: 2px; background: var(--orange); }

  .card--front .brand-block { position: absolute; left: 60px; top: 58px; }
  .card--front .brand__name { color: var(--ink); }
  .card--front .brand-bar { margin: 12px 0 0 48px; width: 420px; }

  .person { position: absolute; left: 60px; top: 160px; }
  .person__name {
    font-weight: 700; font-size: 22px; color: var(--ink);
    letter-spacing: 1px; text-transform: uppercase;
  }
  .person__title { font-size: 14px; color: var(--orange); margin-top: 2px; }

  .contacts { position: absolute; left: 60px; top: 228px; list-style: none; }
  .contacts li {
    display: flex; align-items: center; gap: 10px;
    font-size: 14px; color: var(--ink-soft); margin-bottom: 8px;
  }
  .icon { width: 16px; height: 16px; flex: none; }

  .divider {
    position: absolute; left: 318px; top: 158px;
    width: 1px; height: 62px; background: var(--orange);
  }

  .address {
    position: absolute; left: 336px; top: 156px;
    display: flex; gap: 10px;
    font-size: 14px; line-height: 1.5; color: var(--ink-soft);
  }
  .address .icon { margin-top: 2px; }

  .card--back .brand-block {
    position: absolute; left: 50%; top: 160px;
    transform: translateX(-50%);
  }
  .card--back .brand__name { color: var(--white); }
  .card--back .brand-bar { margin: 12px 0 0 auto; width: 200px; }
  .website {
    position: absolute; left: 50px; bottom: 40px;
    font-size: 14px; color: var(--white);
  }
  .website span { color: var(--orange); }
</style>
</head>
<body>

<section class="card card--front" aria-label="Business card front">
  <svg class="swoosh" viewBox="0 0 700 400" preserveAspectRatio="none" aria-hidden="true">
    <path d="M0 400 L0 388 C300 381 600 303 684 0 L700 0 L700 400 Z" fill="var(--orange)"/>
    <path d="M0 380 C296 372 590 296 664 0 L676 0 C598 300 300 378 0 386 Z" fill="var(--charcoal)"/>
  </svg>

  <div class="brand-block">
    <div class="brand">
      <span class="brand__dot"></span>
      <span class="brand__name">Korvanta Translations</span>
    </div>
    <div class="brand-bar"></div>
  </div>

  <div class="person">
    <div class="person__name">Gordon R. Quell</div>
    <div class="person__title">Director</div>
  </div>

  <ul class="contacts">
    <li>
      <svg class="icon" viewBox="0 0 16 16"><circle cx="8" cy="8" r="8" fill="var(--orange)"/><path d="M5 4.5l1.5 0 .8 2-1 .8a5 5 0 002.4 2.4l.8-1 2 .8v1.5c0 .5-.5 1-1 1A7 7 0 014 5.5c0-.5.5-1 1-1z" fill="#fff"/></svg>
      +1-888-604-7321
    </li>
    <li>
      <svg class="icon" viewBox="0 0 16 16"><rect x="1" y="3" width="14" height="10" rx="1" fill="var(--orange)"/><path d="M1.5 4l6.5 5 6.5-5" stroke="#fff" stroke-width="1.2" fill="none"/></svg>
      jquell@korvantatranslations.example
    </li>
    <li>
      <svg class="icon" viewBox="0 0 16 16"><circle cx="8" cy="8" r="7" fill="var(--orange)"/><path d="M1 8h14M8 1c-3 3-3 11 0 14M8 1c3 3 3 11 0 14" stroke="#fff" stroke-width="1" fill="none"/></svg>
      www.korvantatranslations.example
    </li>
  </ul>

  <div class="divider"></div>

  <div class="address">
    <svg class="icon" viewBox="0 0 16 16"><path d="M8 1a5 5 0 00-5 5c0 4 5 9 5 9s5-5 5-9a5 5 0 00-5-5z" fill="var(--orange)"/><circle cx="8" cy="6" r="2" fill="#fff"/></svg>
    <div>#207-2836 Wexholm Avenue,<br>Victoria, BC,<br>Canada V9T3K2</div>
  </div>
</section>

<section class="card card--back" aria-label="Business card back">
  <div class="brand-block">
    <div class="brand">
      <span class="brand__dot"></span>
      <span class="brand__name">Korvanta Translations</span>
    </div>
    <div class="brand-bar"></div>
  </div>
  <div class="website">www.<span>korvantatranslations</span>.example</div>
</section>

</body>
</html>
```